Anzeigenerstellung für ein Hochglanzmagazin
Zielgruppe
Männer und Frauen, junge Familien bis hin zum Senior.
Verkauf von hochwertigen Immobilien in Spanien.
Aufgabenstellung
Wir benötigen ein schönes und frisches Anzeigendesign, gerne im Magazinstil mit einem Luxus-Touch. Es handelt sich hierbei um eine Imageanzeige, nicht um eine spezifische Immobilienanzeige. Wir sind eine skandinavische Agentur für Luxus-Immobilien auf Mallorca. Das Design sollte dementsprechend edel aber dennoch schlicht gestaltet sein!

```html
<!DOCTYPE html>
<html lang="en">
<head>
<meta charset="utf-8">
<title>Solvik Homes – Luxury Real Estates for Mallorca &amp; Ibiza</title>
<link rel="stylesheet" href="https://fonts.googleapis.com/css2?family=Ubuntu:wght@300;400&display=swap">
<style>
  :root {
    --navy: #15375e;
    --band: rgba(228, 239, 250, 0.86);
    --sky-top: #3f86d6;
    --sky-low: #b9d3ec;
    --sea: #1d4f9a;
    --terrace: #b8b4ae;
    --terrace-low: #a29d97;
  }
  html, body {
    margin: 0;
    padding: 0;
    overflow: hidden;
    background: #ffffff;
  }
  .ad {
    position: relative;
    width: 931px;
    height: 1200px;
    overflow: hidden;
    font-family: "Ubuntu", sans-serif;
    color: var(--navy);
  }
  .ad__photo {
    position: absolute;
    inset: 0;
    background: linear-gradient(180deg,
      var(--sky-top) 0%,
      var(--sky-low) 48%,
      var(--sea) 52%,
      var(--sea) 60%,
      var(--terrace) 64%,
      var(--terrace-low) 100%);
  }
  .headline {
    position: absolute;
    top: 0;
    left: 0;
    width: 100%;
    margin: 0;
    font-weight: 400;
    font-size: 49px;
    letter-spacing: 1px;
  }
  .headline__band {
    position: absolute;
    right: 0;
    height: 64px;
    line-height: 66px;
    padding-right: 142px;
    text-align: right;
    background: var(--band);
    box-sizing: border-box;
  }
  .headline__band--1 { top: 125px; left: 578px; }
  .headline__band--2 { top: 201px; left: 647px; }
  .headline__band--3 { top: 274px; left: 553px; }
  .headline__band--4 { top: 348px; left: 680px; }
  .headline__band--5 { top: 420px; left: 507px; }
  .headline__band--6 { top: 492px; left: 598px; }
  .brand {
    position: absolute;
    top: 1018px;
    right: 168px;
    font-size: 35px;
    font-weight: 400;
    letter-spacing: 0.5px;
    color: var(--navy);
  }
  .contact {
    position: absolute;
    right: 142px;
    top: 1074px;
    text-align: right;
    font-size: 13px;
    font-style: normal;
    font-weight: 400;
    line-height: 27px;
    color: var(--navy);
  }
  .contact p { margin: 0; }
</style>
</head>
<body>
<main class="ad">
  <div class="ad__photo" role="img" aria-label="Photo of a whitewashed Mediterranean villa terrace overlooking the blue sea under a bright sky, with a grey dog resting on the terrace"></div>

  <h1 class="headline">
    <span class="headline__band headline__band--1">LUXURY</span>
    <span class="headline__band headline__band--2">REAL</span>
    <span class="headline__band headline__band--3">ESTATES</span>
    <span class="headline__band headline__band--4">FOR</span>
    <span class="headline__band headline__band--5">MALLORCA</span>
    <span class="headline__band headline__band--6">&amp; IBIZA</span>
  </h1>

  <div class="brand">Solvik Homes</div>

  <address class="contact">
    <p>C. Solmar 12</p>
    <p>07180 Portals Spain | Tel. 971 400 218</p>
    <p>info@solvikhomes.com | www.solvikhomes.com</p>
  </address>
</main>
</body>
</html>
```